Start-up braucht modernes/hochwertiges Getränkeetikett
Zielgruppe
Wir sind ein modernes, nachhaltiges Start-up, welches eine neue Getränkekategorie auf den Markt bringt. Ein sogenanntes Elektrolyt-Getränk mit dem Namen FLUXO4. Es ist abgefüllt in eine 500 ml Flasche und enthält Magnesium, Kalzium, Kalium, und Natrium. Diese Stoffe (Elektrolyte) dienen der körperlichen Hydrierung. Zu Dehydrierung kann es durch Hitze, Alkohol, Sport oder Krankheit kommen. Krankheit liegt bei uns allerdings nicht im Fokus. In unserer Zielgruppe befinden sich hauptsächlich Personen im Alter von 18 - 29 Jahren.
Die Geschmacksrichtung ist Zitrone-Limette.
Aufgabenstellung
Das Etikett soll:
- MODERN, SCHLICHT und HOCHWERTIG sein, so dass es im Supermarkt hervorsticht
- erkenntlich machen, dass die Stoffe Magnesium, Natrium, Kalzium und Kalium enthalten sind
- sich farblich deutlich von der Farbe des Inhalts (weiß) abheben. (Vorzugsweise mit einem hellen Blau, türkis)
- für unsere junge Zielgruppe ansprechend sein
- ebenfalls auf die Geschmacksrichtung (Zitrone-Limette) hinweisen, und zwar so, dass wenn man eine weitere Geschmacksrichtung auf den Markt bringen möchte, diese leicht angepasst werden kann.
- nicht nach einem Energydrink oder einem typischen Sportgetränk aussehen
- unter dem Namen den Slogan 'Elektrolyt-Getränk' stehen haben
-Das Etikett ist nicht dursichtig sondern besteht aus Papier
Der Name sowie das Logo können selbstverständlich farblich verändert werden. Bei dem Logo können auch größere Änderungen vollzogen werden.
Bitte beachten Sie die unten zu stehenden Regler um sich einen guten Überblick über unsere Vorstellungen zu verschaffen. Die Platzierung des EAN-Code ist für ihr Design irrelevat .
Bei Unklarheiten gerne nachfragen!

```html
<!DOCTYPE html>
<html lang="de">
<head>
<meta charset="utf-8">
<title>FLUXO4 Elektrolyte – Etikettenreihe</title>
<link href="https://fonts.googleapis.com/css2?family=Jost:wght@300;400;800&family=Oswald:wght@600&display=swap" rel="stylesheet">
<style>
  :root {
    --page: #f4f6f8;
    --field-deep: #4596cf;
    --field-light: #6ab1df;
    --white: #ffffff;
    --mineral-disc: #e9f3f9;
  }
  * { box-sizing: border-box; margin: 0; padding: 0; }
  html, body {
    width: 1200px; height: 1060px; overflow: hidden;
    background: var(--page);
    font-family: "Jost", sans-serif;
  }
  .label-range {
    position: absolute; left: 30px; top: 265px;
    display: flex; gap: 30px;
  }
  .label {
    position: relative; width: 360px; height: 530px; overflow: hidden;
    color: var(--white);
    box-shadow: 0 6px 18px rgba(0,0,0,.12);
  }
  .label__ground { position: absolute; inset: 0; width: 100%; height: 100%; }
  .brand {
    position: absolute; top: 18px; left: 0; width: 100%; text-align: center;
    font-weight: 800; font-size: 30px; letter-spacing: 0.5px; line-height: 1;
    padding-left: 10px;
  }
  .tagline {
    position: absolute; top: 56px; left: 0; width: 100%; text-align: center;
    font-weight: 300; font-size: 12px; letter-spacing: 5px; line-height: 1;
    padding-left: 10px; white-space: nowrap;
  }
  .category {
    position: absolute; top: 194px; left: 58px;
    font-family: "Oswald", sans-serif; font-weight: 600;
    font-size: 38px; letter-spacing: 7px; line-height: 1; white-space: nowrap;
  }
  .benefits {
    position: absolute; top: 248px; left: 60px;
    font-weight: 400; font-size: 17px; line-height: 22px; white-space: nowrap;
  }
  .mineral-disc {
    position: absolute; left: 236px; top: 238px; width: 78px; height: 78px;
    border-radius: 50%; background: var(--mineral-disc);
    border: 2px solid var(--white);
  }
  .claim {
    position: absolute; top: 432px; left: 58px;
    font-size: 22px; font-weight: 300; line-height: 1.2; white-space: nowrap;
  }
  .claim strong { font-weight: 800; letter-spacing: 0.5px; }
  .flavour {
    position: absolute; top: 489px; left: 0; width: 100%; text-align: center;
    font-size: 13px; font-weight: 300; line-height: 1.2; padding-left: 4px;
  }
</style>
</head>
<body>
<main class="label-range">

  <section class="label label--lemon">
    <svg class="label__ground" viewBox="0 0 360 530" aria-hidden="true">
      <defs>
        <linearGradient id="band-lemon" x1="0" x2="1" y1="0" y2="0">
          <stop offset="0" stop-color="#c8940e"/><stop offset="1" stop-color="#ffd800"/>
        </linearGradient>
        <linearGradient id="field-lemon" x1="0" x2="1" y1="1" y2="0">
          <stop offset="0" stop-color="#4596cf"/><stop offset="1" stop-color="#6ab1df"/>
        </linearGradient>
      </defs>
      <rect width="360" height="530" fill="url(#band-lemon)"/>
      <path d="M138 0H360V530H140V470C140 425 118 400 78 392C40 385 20 370 20 338V205C20 178 38 166 72 160C112 152 138 130 138 100Z" fill="url(#field-lemon)"/>
    </svg>
    <div class="brand">FLUXO4</div>
    <div class="tagline">KEEP YOUR BALANCE</div>
    <div class="category">ELEKTROLYTE</div>
    <p class="benefits">Mehr Ausdauer<br>Mehr Konzentration</p>
    <div class="mineral-disc" role="img" aria-label="Hinweis auf Magnesium, Kalzium, Kalium und Natrium"></div>
    <div class="claim"><strong>ZERO</strong> Calorie &amp; Sugar</div>
    <div class="flavour">ZITRONE/LIMETTE</div>
  </section>

  <section class="label label--peach">
    <svg class="label__ground" viewBox="0 0 360 530" aria-hidden="true">
      <defs>
        <linearGradient id="band-peach" x1="0" x2="1" y1="0" y2="0">
          <stop offset="0" stop-color="#c2620a"/><stop offset="1" stop-color="#f7a70c"/>
        </linearGradient>
        <linearGradient id="field-peach" x1="0" x2="1" y1="1" y2="0">
          <stop offset="0" stop-color="#4596cf"/><stop offset="1" stop-color="#6ab1df"/>
        </linearGradient>
      </defs>
      <rect width="360" height="530" fill="url(#band-peach)"/>
      <path d="M138 0H360V530H140V470C140 425 118 400 78 392C40 385 20 370 20 338V205C20 178 38 166 72 160C112 152 138 130 138 100Z" fill="url(#field-peach)"/>
    </svg>
    <div class="brand">FLUXO4</div>
    <div class="tagline">KEEP YOUR BALANCE</div>
    <div class="category">ELEKTROLYTE</div>
    <p class="benefits">Mehr Ausdauer<br>Mehr Konzentration</p>
    <div class="mineral-disc" role="img" aria-label="Hinweis auf Magnesium, Kalzium, Kalium und Natrium"></div>
    <div class="claim"><strong>ZERO</strong> Calorie &amp; Sugar</div>
    <div class="flavour">PEACH</div>
  </section>

  <section class="label label--apple">
    <svg class="label__ground" viewBox="0 0 360 530" aria-hidden="true">
      <defs>
        <linearGradient id="band-apple" x1="0" x2="1" y1="0" y2="0">
          <stop offset="0" stop-color="#b3ad08"/><stop offset="1" stop-color="#cfd51a"/>
        </linearGradient>
        <linearGradient id="field-apple" x1="0" x2="1" y1="1" y2="0">
          <stop offset="0" stop-color="#4596cf"/><stop offset="1" stop-color="#6ab1df"/>
        </linearGradient>
      </defs>
      <rect width="360" height="530" fill="url(#band-apple)"/>
      <path d="M138 0H360V530H140V470C140 425 118 400 78 392C40 385 20 370 20 338V205C20 178 38 166 72 160C112 152 138 130 138 100Z" fill="url(#field-apple)"/>
    </svg>
    <div class="brand">FLUXO4</div>
    <div class="tagline">KEEP YOUR BALANCE</div>
    <div class="category">ELEKTROLYTE</div>
    <p class="benefits">Mehr Ausdauer<br>Mehr Konzentration</p>
    <div class="mineral-disc" role="img" aria-label="Hinweis auf Magnesium, Kalzium, Kalium und Natrium"></div>
    <div class="claim"><strong>ZERO</strong> Calorie &amp; Sugar</div>
    <div class="flavour">APFEL/MINT</div>
  </section>

</main>
</body>
</html>
```